Business card for Luxury Portable Restroom Trailer company

We are a Luxury Portable Restroom Trailer Company Called FALCRIDGE HIRES. Based in Orange County California. We provide portable restroom trailers for events, such as, Weddings, Concerts, Charity events, Sporting events, Tournaments, Corporate events, ect. We rent and Sell the Luxury restrooms. Our colors are white, grey, and Orange. As you will see in the logo we uploaded.
There are 2 people in the company so the names and titles will change for the 3 people but card will remain the same. Here is the information for each Person: Dwight Penner CFO 555 318-0476
next Person: Leon Marchetti VP 555 318-0476
Next Person: Owen Marchetti CEO 555 318-0476
Information to include on the card: Luxury Restroom Trailers Rental and Sales. Weddings, Concerts, Charity, Sporting and Corp. Events.

```html
<!DOCTYPE html>
<html lang="en">
<head>
<meta charset="utf-8">
<title>Falcridge Hires – Business Card</title>
<link href="https://fonts.googleapis.com/css2?family=Montserrat:wght@500;600;800&display=swap" rel="stylesheet">
<style>
  :root {
    --orange: #f26f23;
    --grey: #58595b;
    --ink: #2b2b2b;
    --white: #ffffff;
    --backdrop: #e4e4e4;
  }
  * { box-sizing: border-box; margin: 0; padding: 0; }
  html, body { width: 1200px; height: 880px; overflow: hidden; }
  body {
    background: var(--backdrop);
    font-family: "Montserrat", sans-serif;
    display: flex;
    flex-direction: column;
    align-items: center;
    justify-content: center;
    gap: 36px;
  }
  .card {
    position: relative;
    width: 700px;
    height: 400px;
    background: var(--white);
    box-shadow: 0 6px 18px rgba(0,0,0,.18);
    overflow: hidden;
  }

  /* Front */
  .card-front {
    display: flex;
    flex-direction: column;
    align-items: center;
    justify-content: center;
    gap: 34px;
  }
  .brand-frame {
    border: 5px solid var(--grey);
    padding: 30px 44px;
    display: flex;
    align-items: center;
    gap: 18px;
  }
  .brand-mark {
    width: 34px; height: 34px;
    border-radius: 50%;
    background: var(--orange);
  }
  .brand-name {
    font-weight: 800;
    font-size: 46px;
    letter-spacing: 2px;
    color: var(--grey);
    line-height: 1;
  }
  .services {
    text-align: center;
    font-weight: 500;
    font-size: 16px;
    color: var(--ink);
    line-height: 1.7;
  }
  .services li { list-style: none; display: inline; margin: 0 6px; }
  .services li::before {
    content: "";
    display: inline-block;
    width: 9px; height: 9px;
    border-radius: 50%;
    background: var(--orange);
    margin-right: 7px;
    vertical-align: 1px;
  }

  /* Back */
  .seal {
    position: absolute;
    left: 100px; top: 50px;
    width: 200px; height: 200px;
    border: 12px solid var(--orange);
    border-radius: 50%;
    display: flex;
    align-items: center;
    justify-content: center;
    text-align: center;
  }
  .seal-name {
    font-weight: 800;
    font-size: 22px;
    line-height: 1.2;
    letter-spacing: 1px;
    color: var(--orange);
  }
  .divider {
    position: absolute;
    left: 378px; top: 58px;
    width: 2px; height: 180px;
    background: var(--orange);
  }
  .contacts {
    position: absolute;
    left: 400px; top: 34px;
    display: flex;
    flex-direction: column;
    gap: 10px;
  }
  .person-name {
    font-weight: 800;
    font-size: 19px;
    color: var(--grey);
    text-transform: uppercase;
    letter-spacing: .5px;
    line-height: 1.25;
  }
  .person-name .surname { color: var(--orange); }
  .person-role, .person-phone {
    font-weight: 500;
    font-size: 14px;
    color: var(--ink);
    line-height: 1.35;
  }
  .person-phone { display: flex; align-items: center; gap: 7px; }
  .phone-icon { width: 14px; height: 14px; fill: var(--orange); }
  .wave { position: absolute; left: 0; bottom: 0; width: 700px; height: 110px; }
</style>
</head>
<body>

<section class="card card-front">
  <div class="brand-frame">
    <span class="brand-mark"></span>
    <span class="brand-name">FALCRIDGE HIRES</span>
  </div>
  <ul class="services">
    <li>Luxury Restroom Trailers Rental and Sales</li><br>
    <li>Weddings</li><li>Concerts</li><li>Charity</li><li>Sporting and Corp</li><li>Events</li>
  </ul>
</section>

<section class="card card-back">
  <div class="seal"><span class="seal-name">FALCRIDGE<br>HIRES</span></div>
  <div class="divider"></div>
  <div class="contacts">
    <div class="person">
      <p class="person-name">Dwight <span class="surname">Penner</span></p>
      <p class="person-role">CFO</p>
      <p class="person-phone"><svg class="phone-icon" viewBox="0 0 24 24"><path d="M2 9c3-4 17-4 20 0l-1 3-4-1v-2c-3-1-7-1-10 0v2l-4 1zM6 13h12l2 7H4z"/></svg>555 318-0476</p>
    </div>
    <div class="person">
      <p class="person-name">Leon <span class="surname">Marchetti</span></p>
      <p class="person-role">VP</p>
      <p class="person-phone"><svg class="phone-icon" viewBox="0 0 24 24"><path d="M2 9c3-4 17-4 20 0l-1 3-4-1v-2c-3-1-7-1-10 0v2l-4 1zM6 13h12l2 7H4z"/></svg>555 318-0476</p>
    </div>
    <div class="person">
      <p class="person-name">Owen <span class="surname">Marchetti</span></p>
      <p class="person-role">CEO</p>
      <p class="person-phone"><svg class="phone-icon" viewBox="0 0 24 24"><path d="M2 9c3-4 17-4 20 0l-1 3-4-1v-2c-3-1-7-1-10 0v2l-4 1zM6 13h12l2 7H4z"/></svg>555 318-0476</p>
    </div>
  </div>
  <svg class="wave" viewBox="0 0 700 110" preserveAspectRatio="none">
    <path d="M0 62 C 220 58, 340 40, 470 22 C 570 8, 650 2, 700 0 L700 6 C 640 8, 560 16, 460 34 C 330 58, 200 70, 0 74 Z" fill="var(--grey)"/>
    <path d="M0 82 C 210 80, 340 64, 470 38 C 570 20, 650 12, 700 10 L700 110 L0 110 Z" fill="var(--orange)"/>
  </svg>
</section>

</body>
</html>
```